New Fun, Positive, energised looking Business Card Needed for High Achiever Coach

I am looking for a two sided full colour business card. I am self employed and have recently re branded my 1-2-1 work re-vitalising high achievers. My target client base for these cards is therefore high achievers - usually aged 40 -55, they are often entrepreneurs, CEO or work in banking and finance and 2/3 are male. I work with them on 90 day or 6 month coaching programs to help them live their success in a healthier, more sustainable and fulfiiled way. They pay for this privately so though they are corporate types the cards need not look 'corporate'. I want to portray the idea of transformation, vitality and re-connecting.
You can get a feel for the look I like on my new website: morvenlisk.co.uk
I want to use this logo with strapline (Re-Vitalising High Achievers) (I purchased off Logoharbor) and font/ colours (the turquoise and green).
Details to include on the card:
www.morvenlisk.co.uk
+44 7915 302618
morven@morvenlisk.co.uk
skype: morvenlisk
I'd also like to include:
Do you struggle to switch off? Want to be healthier and feel fitter? Want closer relationships? More clarity over the direction you are headed? I can help you do these things using integrated mind-body techniques. Visit morvenlisk.co.uk TODAY to apply for a FREE Breakthrough session.
BUT if that is too much text for a card I am open to advice/ammendments.
Updates
Thanks for your design - I am considering them. PLease change the wording to :

```html
<!DOCTYPE html>
<html lang="en">
<head>
<meta charset="utf-8">
<title>Morven Lisk – Business Card</title>
<link rel="stylesheet" href="https://fonts.googleapis.com/css2?family=Open+Sans:wght@400;700;800&display=swap">
<style>
  :root {
    --turquoise: #0aa3c6;
    --turquoise-dark: #0891b2;
    --green: #5cb85c;
    --white: #ffffff;
    --ink: #2a2a2a;
    --backdrop: #e9eaee;
    --card-w: 740px;
    --card-h: 423px;
  }
  * { box-sizing: border-box; margin: 0; padding: 0; }
  html, body {
    width: 1200px; height: 987px; overflow: hidden;
    background: var(--backdrop);
    font-family: "Open Sans", Arial, sans-serif;
  }
  .sheet {
    width: 1200px; height: 987px;
    display: flex; flex-direction: column; align-items: center; justify-content: center;
    gap: 44px;
  }
  .card {
    position: relative;
    width: var(--card-w); height: var(--card-h);
    border-radius: 22px; overflow: hidden;
    box-shadow: 0 6px 18px rgba(0,0,0,.12);
  }

  /* Front */
  .card--front { background: var(--white); }
  .front__band {
    position: absolute; left: 0; right: 0; top: 150px; height: 212px;
    background: var(--turquoise);
  }
  .brand {
    position: absolute; left: 0; right: 0; top: 166px;
    display: flex; align-items: center; justify-content: center; gap: 14px;
  }
  .brand__dot { width: 30px; height: 30px; border-radius: 50%; background: var(--green); }
  .brand__name {
    font-weight: 800; font-size: 44px; color: var(--white); letter-spacing: .5px; line-height: 1;
  }
  .strapline {
    position: absolute; left: 0; right: 0; top: 222px; text-align: center;
    font-size: 17px; color: var(--white); letter-spacing: .5px;
  }
  .contacts {
    position: absolute; left: 0; right: 0; top: 268px;
    display: flex; flex-direction: column; align-items: center; gap: 14px;
    color: var(--white); font-size: 20px;
  }
  .contacts__row { display: flex; gap: 26px; }
  .contact { display: flex; align-items: center; gap: 8px; }
  .contact svg { width: 20px; height: 20px; }
  .contact__square { width: 17px; height: 17px; border: 2px solid var(--white); border-radius: 3px; }
  .website {
    position: absolute; left: 0; right: 0; top: 374px; text-align: center;
    font-size: 24px; color: var(--ink); letter-spacing: 1.5px;
  }
  .website__domain { color: var(--turquoise); }

  /* Back */
  .card--back {
    background: var(--turquoise);
    display: flex; align-items: center; justify-content: center;
  }
  .pitch {
    text-align: center; color: var(--white);
    font-size: 22px; line-height: 1.36;
  }
  .pitch strong { font-weight: 700; }
</style>
</head>
<body>
<main class="sheet">
  <section class="card card--front" aria-label="Card front">
    <div class="front__band"></div>
    <div class="brand">
      <span class="brand__dot"></span>
      <span class="brand__name">Morven Lisk</span>
    </div>
    <p class="strapline">Re-Vitalising High Achievers</p>
    <div class="contacts">
      <div class="contact">
        <svg viewBox="0 0 20 20" aria-hidden="true">
          <circle cx="10" cy="10" r="8.5" fill="none" stroke="#fff" stroke-width="1.6"/>
          <path d="M7 5.5c-.8.6-1.2 1.6-.7 3 .7 2 2.5 4 4.6 5 1.2.5 2.1.3 2.8-.4l-1.6-1.6-1.2.6c-1-.5-2-1.5-2.5-2.6l.6-1.2z" fill="#fff"/>
        </svg>
        <span>+44 7915 302618</span>
      </div>
      <div class="contacts__row">
        <div class="contact"><span class="contact__square"></span><span>morvenlisk</span></div>
        <div class="contact">
          <svg viewBox="0 0 20 20" aria-hidden="true">
            <rect x="2" y="5" width="16" height="11" rx="1.5" fill="none" stroke="#fff" stroke-width="1.6"/>
            <path d="M2.5 5.5 10 11l7.5-5.5" fill="none" stroke="#fff" stroke-width="1.6"/>
          </svg>
          <span>morven@morvenlisk.co.uk</span>
        </div>
      </div>
    </div>
    <p class="website">www.<span class="website__domain">morvenlisk</span>.co.uk</p>
  </section>

  <section class="card card--back" aria-label="Card back">
    <p class="pitch">
      Do you struggle to switch off?<br>
      Want to be healthier and feel fitter?<br>
      Want closer relationships?<br>
      More clarity over the direction you are headed?<br>
      I can help you do these things using integrated<br>
      mind-body techniques.<br>
      Visit <strong>morvenlisk.co.uk</strong> TODAY to apply for a<br>
      FREE Breakthrough session.
    </p>
  </section>
</main>
</body>
</html>
```